Modern Medical Optometry Website

We need mordern, Patient friendly website. Easy to navigate and enhance our advance medical technology and excellent patient care.
1. HOME PAGE
2. OUR TEAM PAGE
3. EYECARE PAGE - VISION SERVICES, EYE EXAMS, KERATOCONUS CENTER, GLAUCOMA , DIABITES, MELORIDEX EXAM, DIGITAL RETINAL, OCT.
4. MYOPIA CONTROL CLINIC
5. DRY EYE CLINIC
6. EYEWEAR
7. PATIENT CENTER - BLOG
7. CONTACT US
This is our current website www.brivaloka.com
and We want to add more content and a cleaner design like these website
http://tarnwickfolvendale.com/
https://www.qmvorlu.com/

```html
<!DOCTYPE html>
<html lang="en">
<head>
<meta charset="utf-8">
<title>Lumora Optometry</title>
<link rel="stylesheet" href="https://fonts.googleapis.com/css2?family=Poppins:wght@400;500;600;700&family=Open+Sans:wght@400;600;700&display=swap">
<style>
:root{
  --yellow:#fbcd33;
  --hero-a:#fdb813;
  --hero-b:#ffc21a;
  --ink:#1b1b1b;
  --heading:#3f3f3f;
  --text:#333333;
  --white:#ffffff;
  --btn:#f9cb36;
}
*{margin:0;padding:0;box-sizing:border-box}
html,body{width:1200px;height:2808px;overflow:hidden;background:var(--white)}
body{position:relative;font-family:"Open Sans",sans-serif;color:var(--text)}
.abs{position:absolute}
.photo{position:absolute;display:block}

/* hero */
.hero{position:absolute;left:0;top:0;width:1200px;height:593px;background:linear-gradient(90deg,var(--hero-a),var(--hero-b) 60%,#ffb70f);overflow:hidden}
.hero-photo{left:90px;top:40px;width:460px;height:553px;background:radial-gradient(ellipse at 50% 45%,#e8e3dc 0%,#5a5a72 45%,rgba(253,184,19,0) 72%)}
.brand-box{position:absolute;left:99px;top:0;width:98px;height:125px;background:var(--white);display:flex;align-items:center;justify-content:center;flex-direction:column;gap:6px}
.brand-box .mark{width:14px;height:14px;background:var(--yellow)}
.brand-box .name{font-family:"Poppins",sans-serif;font-weight:500;font-size:11px;color:#e0a800;text-align:center;line-height:1.25;letter-spacing:.5px}
.main-nav{position:absolute;left:315px;top:38px;display:flex;gap:0;width:780px;justify-content:space-between}
.main-nav a{font-family:"Poppins",sans-serif;font-weight:500;font-size:12.5px;color:var(--ink);text-decoration:none;text-transform:uppercase}
.hero-title{position:absolute;right:190px;top:180px;font-family:"Poppins",sans-serif;font-weight:600;font-size:82px;line-height:1;color:var(--white);letter-spacing:-1px}
.hero-phone{position:absolute;right:190px;top:270px;font-family:"Poppins",sans-serif;font-weight:600;font-size:42px;line-height:1;color:var(--white)}
.btn-dark{position:absolute;left:779px;top:339px;width:226px;height:47px;border-radius:24px;background:var(--ink);color:var(--white);font-family:"Poppins",sans-serif;font-weight:600;font-size:16px;display:flex;align-items:center;justify-content:center}
.dots{position:absolute;left:544px;top:518px;display:flex;gap:21px}
.dots span{width:12px;height:12px;border-radius:50%;background:#f7e23a}
.dots span:nth-child(3){background:var(--white)}

/* intro */
.intro-photo{left:112px;top:625px;width:307px;height:397px;background:linear-gradient(160deg,#6c7a6a,#c9a58b 45%,#5b8ac0)}
.col-title{position:absolute;font-family:"Poppins",sans-serif;font-weight:700;font-size:37px;line-height:44px;color:var(--heading);text-transform:uppercase}
.col-text{position:absolute;width:305px;font-size:14.6px;line-height:25.6px;color:var(--text)}
.btn-read{position:absolute;width:114px;height:36px;border-radius:8px;background:var(--btn);font-family:"Poppins",sans-serif;font-weight:600;font-size:16px;color:var(--ink);display:flex;align-items:center;justify-content:center}

/* team */
.team-photo{left:0;top:1089px;width:1200px;height:416px;background:linear-gradient(180deg,#b7b88a 0%,#c8c39a 35%,#3c4660 75%,#2a3350 100%)}
.team-band{position:absolute;left:0;top:1505px;width:1200px;height:124px;background:var(--yellow);display:flex;align-items:center;justify-content:center;font-family:"Poppins",sans-serif;font-weight:600;font-size:40px;color:var(--heading)}
.notch{position:absolute;left:572px;top:1479px}

/* eyecare */
.section-title{position:absolute;font-family:"Poppins",sans-serif;font-weight:700;color:var(--heading)}
.tile{position:absolute;top:1668px;width:314px;height:371px;display:flex;align-items:center;justify-content:center}
.tile span{font-family:"Open Sans",sans-serif;font-weight:700;font-size:39px;color:var(--white);letter-spacing:.5px}
.tile-diabetes{left:440px;background:linear-gradient(160deg,#4f3d33,#a98a6f 50%,#6d5545)}
.tile-exams{left:777px;background:linear-gradient(160deg,#7c8890,#b3a7a0 50%,#5a4d57)}

/* patient center */
.patient{position:absolute;left:0;top:2119px;width:1200px;height:535px;background:var(--yellow)}
.card-img{position:absolute;top:2274px;height:201px}
.card-img.one{left:112px;width:307px;background:linear-gradient(135deg,#dfe6ec,#4f5f8c 55%,#c4cdd6)}
.card-img.two{left:446px;width:308px;background:linear-gradient(135deg,#3a2a26,#b4826b 55%,#2e2624)}
.card-img.three{left:779px;width:307px;background:linear-gradient(135deg,#a99385,#d7c2b3 55%,#8a7a72)}
.card{position:absolute;top:2428px;height:165px;background:var(--white);text-align:center}
.card h3{margin-top:22px;font-family:"Open Sans",sans-serif;font-weight:700;font-size:19px;color:var(--ink);text-transform:uppercase}
.card p{margin:10px auto 0;width:230px;font-size:11.5px;line-height:21px;color:var(--text)}
.card .plus{position:absolute;left:50%;top:142px;transform:translateX(-50%);font-size:22px;line-height:1;color:var(--ink)}
.card .plus-box{position:absolute;left:50%;top:122px;width:30px;height:30px;transform:translateX(-50%);background:var(--ink);color:var(--white);font-size:22px;display:flex;align-items:center;justify-content:center}
.card .bar{position:absolute;left:50%;bottom:-4px;width:32px;height:5px;transform:translateX(-50%);background:var(--ink)}

/* footer */
.footer-nav{position:absolute;left:212px;top:2693px;width:775px;display:flex;justify-content:space-between}
.footer-nav a{font-family:"Poppins",sans-serif;font-weight:500;font-size:12.5px;color:var(--ink);text-decoration:none;text-transform:uppercase}
.copyright{position:absolute;left:0;top:2728px;width:1200px;text-align:center;font-family:"Poppins",sans-serif;font-size:12.5px;color:#444}
.social{position:absolute;left:536px;top:2766px;display:flex;gap:24px}
.social span{width:11px;height:11px;border-radius:50%;background:var(--ink)}
</style>
</head>
<body>

<header class="hero">
  <div class="photo hero-photo" role="img" aria-label="Smiling bearded man in sunglasses, hat and striped polo shirt giving a thumbs up"></div>
  <div class="brand-box"><span class="mark"></span><span class="name">LUMORA<br>OPTOMETRY</span></div>
  <nav class="main-nav">
    <a href="#">Home</a><a href="#">Our Team</a><a href="#">Eyecare</a><a href="#">Myopia Control Clinic</a><a href="#">Dry Eye Clinic</a><a href="#">Eyewear</a><a href="#">Blog</a><a href="#">Contact Us</a>
  </nav>
  <h1 class="hero-title">lumorasee</h1>
  <div class="hero-phone">555-014-2763</div>
  <a class="btn-dark">Make an Appointment</a>
  <div class="dots"><span></span><span></span><span></span><span></span></div>
</header>

<section class="intro">
  <div class="photo intro-photo" role="img" aria-label="Smiling girl with glasses and a school backpack"></div>
  <h2 class="col-title" style="left:453px;top:628px">The Lumora<br>Promise</h2>
  <p class="col-text" style="left:453px;top:735px">Welcome to Lumora Optometry, where your vision and eye health are our sole priority. We take great pride in providing you with state-of-the-art eyecare matched with personal attention from our staff and doctors. Your quality of life is our goal and we believe that healthy eyesight is vital to achieving it.</p>
  <a class="btn-read" style="left:453px;top:936px">Read more</a>

  <h2 class="col-title" style="left:784px;top:628px">Vision<br>Services</h2>
  <p class="col-text" style="left:784px;top:735px">Our comprehensive eye examinations evaluate your eyes, both inside and out, for any potential disorders or diseases. Your visual skills and abilities are carefully evaluated and appropriate treatment is prescribed - whether it's medication, lenses or low vision rehabilitation.</p>
  <a class="btn-read" style="left:784px;top:936px">Read more</a>
</section>

<section class="team">
  <div class="photo team-photo" role="img" aria-label="Group photo of the clinic staff standing in front of the reception sign"></div>
  <svg class="notch" width="56" height="27" viewBox="0 0 56 27"><polygon points="0,27 28,0 56,27" fill="#fbcd33"/></svg>
  <div class="team-band">Our Team</div>
</section>

<section class="eyecare">
  <h2 class="section-title" style="left:110px;top:1688px;font-size:36px">EYECARE</h2>
  <p class="col-text" style="left:114px;top:1756px;width:310px">Lorem ipsum dolor sit amet, consectetur adipiscing elit, sed do eiusmod tempor incididunt ut labore et dolore magna aliqua. Ut enim ad minim veniam, quis nostrud exercitation ullamco laboris nisi ut aliquip ex ea commodo consequat. Duis aute irure dolor in reprehenderit in</p>
  <a class="btn-read" style="left:114px;top:1969px">Read more</a>
  <div class="tile tile-diabetes" role="img" aria-label="Hand using a blood glucose meter on a wooden table"><span>DIABITES</span></div>
  <div class="tile tile-exams" role="img" aria-label="Young child during an eye examination"><span>EYE EXAMS</span></div>
</section>

<section class="patient">
  <h2 class="section-title" style="left:0;top:52px;width:1200px;text-align:center;font-size:37px">PATIENT CENTER</h2>
</section>
<div class="photo card-img one" role="img" aria-label="Man with glasses reaching for a book in a library"></div>
<div class="photo card-img two" role="img" aria-label="Mother and child wearing glasses hugging"></div>
<div class="photo card-img three" role="img" aria-label="Close-up of a woman's eyes"></div>
<article class="card" style="left:127px;width:279px">
  <h3>Sed ut perspiciatis</h3>
  <p>Lorem ipsum dolor sit amet, consectetur adipiscing elit, sed do eiusmod tempor incididunt ut labore.</p>
  <span class="plus">+</span><span class="bar"></span>
</article>
<article class="card" style="left:461px;width:279px">
  <h3>Sed ut perspiciatis</h3>
  <p>Lorem ipsum dolor sit amet, consectetur adipiscing elit, sed do eiusmod tempor incididunt ut labore.</p>
  <span class="plus-box">+</span>
</article>
<article class="card" style="left:792px;width:277px">
  <h3>Sed ut perspiciatis</h3>
  <p>Lorem ipsum dolor sit amet, consectetur adipiscing elit, sed do eiusmod tempor incididunt ut labore.</p>
  <span class="plus">+</span><span class="bar"></span>
</article>

<footer>
  <nav class="footer-nav">
    <a href="#">Home</a><a href="#">Our Team</a><a href="#">Eyecare</a><a href="#">Myopia Control Clinic</a><a href="#">Dry Eye Clinic</a><a href="#">Eyewear</a><a href="#">Blog</a><a href="#">Contact Us</a>
  </nav>
  <div class="copyright">© 2019 &nbsp;| &nbsp;www.companyname.com</div>
  <div class="social"><span></span><span></span><span></span><span></span></div>
</footer>

</body>
</html>
```